Computer consultant business card

Bexil Software is a newly started computer consulting company. It's a small one-man company that provides mostly Vornix applications but also websites in collaboration with designers. I'm running this company on the side of full time university studies.

I want the final design to be clean and memorable. Be creative! :)

Some inspiration:
http://www.pixelmarta.com/design/48317
http://www.pixelmarta.com/design/2739164/business-card-design-by-frostlynk
http://www.pixelmarta.com/design/604281/business-card-design-by-koralind-vestrabanu

See attachment for my company logo.
Updates

I would like to thank everyone for submitting! I'll need a couple of days to review and ultimately select a design.

Target Market(s)

Non-technical entrepreneurs and small companies.

Industry/Entity Type

University

Requirements
Must have
• My company logo.
In any way, both colors from my logo.
First- and last name, e-mail and phone number.
Double-sided design.
Nice to have
• Something creative with the symbol in my logo

```html
<!DOCTYPE html>
<html lang="en">
<head>
<meta charset="utf-8">
<title>Bexil Software – Business Card</title>
<link href="https://fonts.googleapis.com/css2?family=Open+Sans:wght@400;600&display=swap" rel="stylesheet">
<style>
  :root {
    --brand-blue: #4670b8;
    --brand-blue-light: #8f98d0;
    --ink-dark: #2a2a2e;
    --ink-grey: #6f6f73;
    --band-grey: #6c6c70;
    --card-white: #ffffff;
    --backdrop: #e9e9ec;
  }
  * { margin: 0; padding: 0; box-sizing: border-box; }
  html, body {
    width: 1200px; height: 789px; overflow: hidden;
    background: var(--backdrop);
    font-family: "Open Sans", Arial, sans-serif;
  }
  .canvas { position: relative; width: 1200px; height: 789px; }

  .card {
    position: absolute;
    width: 540px; height: 310px;
    border-radius: 22px;
    overflow: hidden;
    box-shadow: 0 8px 22px rgba(0,0,0,.18);
  }

  /* Front */
  .card-front { left: 70px; top: 80px; background: var(--card-white); }
  .card-front .wave { position: absolute; inset: 0; width: 100%; height: 100%; }
  .brand { position: absolute; display: flex; align-items: center; gap: 12px; }
  .brand-dot { border-radius: 50%; }
  .brand-name { font-weight: 600; letter-spacing: .5px; line-height: 1; }
  .card-front .brand { left: 50px; top: 70px; }
  .card-front .brand-dot { width: 36px; height: 36px; background: var(--brand-blue); }
  .card-front .brand-name { font-size: 46px; color: var(--ink-dark); }

  .contact { position: absolute; left: 318px; top: 92px; list-style: none; }
  .contact li {
    display: flex; align-items: center; gap: 7px;
    font-size: 17px; color: var(--ink-grey); line-height: 25px;
  }
  .contact svg { width: 13px; height: 13px; fill: var(--brand-blue); flex: none; }

  .person { position: absolute; left: 58px; top: 190px; }
  .person-name { font-size: 15px; color: var(--brand-blue); line-height: 20px; }
  .person-role { font-size: 15px; color: var(--ink-grey); line-height: 20px; }

  /* Back */
  .card-back {
    left: 590px; top: 400px;
    background: radial-gradient(circle at 50% 45%, var(--brand-blue-light) 0%, var(--brand-blue) 62%);
  }
  .card-back .brand { left: 50%; top: 112px; transform: translateX(-50%); }
  .card-back .brand-dot { width: 50px; height: 50px; background: var(--card-white); }
  .card-back .brand-name { font-size: 62px; color: var(--card-white); }
  .web { position: absolute; left: 0; right: 0; bottom: 34px; text-align: center; font-size: 15px; color: var(--card-white); }
</style>
</head>
<body>
<main class="canvas">

  <section class="card card-front" aria-label="Business card front">
    <svg class="wave" viewBox="0 0 540 310" preserveAspectRatio="none" aria-hidden="true">
      <path d="M0,240 C170,256 330,200 480,182 C330,206 170,258 0,262Z" fill="var(--band-grey)"/>
      <path d="M0,266 C170,266 340,207 540,186 L540,310 L0,310Z" fill="var(--brand-blue)"/>
    </svg>

    <div class="brand">
      <span class="brand-dot"></span>
      <span class="brand-name">bexil</span>
    </div>

    <ul class="contact">
      <li>
        <svg viewBox="0 0 16 16"><path d="M3.5 1l3 3-1.6 2a9 9 0 0 0 5 5l2-1.6 3 3-2 2.2C7 14.5 1.5 9 1.3 3z"/></svg>
        00-123-4567
      </li>
      <li>
        <svg viewBox="0 0 16 16"><path d="M4 1h8v4H4zM1 6h14v7h-3v2H4v-2H1zm4 5v2h6v-2z"/></svg>
        00-123-4567
      </li>
      <li>
        <svg viewBox="0 0 16 16"><path d="M1 3h14v10H1zm1.5 1.2V12h11V4.2L8 8.6z M2.8 4L8 7.4 13.2 4z" fill-rule="evenodd"/></svg>
        name@bexilsoft.com
      </li>
    </ul>

    <div class="person">
      <p class="person-name">Your Name</p>
      <p class="person-role">Designation</p>
    </div>
  </section>

  <section class="card card-back" aria-label="Business card back">
    <div class="brand">
      <span class="brand-dot"></span>
      <span class="brand-name">bexil</span>
    </div>
    <p class="web">www.bexilsoft.com</p>
  </section>

</main>
</body>
</html>
```